Bry7Legal Letterhead

Need a new letterhead for my law firm.
IDENTIFYING INFORMATION BELOW:
Anselmo R Quintara III
Attorney at Law
Address: 2847 Larkspur Blvd, Ste 300, Dallas, TX 75204
Phone: 877-482-6017
Fax: 469-738-1452
Email: bry@bry7legal.example
Website: www.bry7legal.example

Colors
0054AA
0677BA
7BADD7
CADEEF
E8F1F8

Requirements
Must have
• Logo needs to be on the letterhead, along with identifying information which is included in the project description.

```html
<!DOCTYPE html>
<html lang="en">
<head>
<meta charset="utf-8">
<title>Bry7Legal Letterhead</title>
<link rel="stylesheet" href="https://fonts.googleapis.com/css2?family=Lato:wght@400;700&family=Open+Sans:wght@400;700&family=Raleway:wght@400;700;800&family=Ubuntu:wght@500;700&display=swap">
<style>
  :root {
    --backdrop: #e4e6e8;
    --ink: #1c1c1c;
    --ink-soft: #3a3a3a;
    --body-grey: #7a7a7a;
    --blue-bright: #1ea7e0;
    --blue-mid: #0677ba;
    --blue-deep: #0054aa;
    --blue-icon: #1a8fd6;
    --signature-tone: #e6e9ed;
  }
  * { margin: 0; padding: 0; box-sizing: border-box; }
  html, body { width: 1127px; height: 1200px; overflow: hidden; background: var(--backdrop); }
  .letterhead {
    position: absolute; left: 153px; top: 20px;
    width: 820px; height: 1160px;
    background: linear-gradient(135deg, #ffffff 40%, #f3f3f3 100%);
    box-shadow: 0 4px 14px rgba(0,0,0,.18);
    font-family: "Lato", sans-serif;
  }
  .brand {
    position: absolute; left: 57px; top: 58px;
    display: flex; align-items: center; gap: 10px;
  }
  .brand-square { width: 22px; height: 22px; background: var(--blue-mid); }
  .brand-name {
    font-family: "Raleway", sans-serif; font-weight: 800;
    font-size: 38px; letter-spacing: 1px; color: var(--ink); line-height: 1;
  }
  .principal {
    position: absolute; right: 46px; top: 64px; text-align: right;
    font-family: "Raleway", sans-serif; color: var(--ink-soft);
  }
  .principal-name { font-weight: 700; font-size: 16px; letter-spacing: .2px; }
  .principal-title { font-size: 11px; margin-top: 3px; }
  .recipient { position: absolute; left: 53px; top: 300px; color: var(--body-grey); }
  .recipient-name {
    font-family: "Ubuntu", sans-serif; font-weight: 700;
    font-size: 18.5px; color: var(--ink-soft); margin-bottom: 7px; letter-spacing: .4px;
  }
  .recipient-line { font-size: 12.3px; line-height: 17.6px; letter-spacing: .15px; }
  .letter-date {
    position: absolute; right: 75px; top: 384px;
    font-size: 12.3px; color: var(--ink); line-height: 17.6px;
  }
  .letter-body {
    position: absolute; left: 51px; top: 438px; width: 723px;
    font-size: 13.1px; line-height: 17.6px; letter-spacing: .15px; color: var(--body-grey);
    text-align: justify;
  }
  .letter-body p + p { margin-top: 18px; }
  .signature {
    position: absolute; left: 80px; top: 787px; width: 201px; height: 40px;
    background: var(--signature-tone); border-radius: 3px;
  }
  .contact-bar {
    position: absolute; left: 51px; top: 1074px; right: 40px;
    font-family: "Open Sans", sans-serif; font-size: 11px; color: var(--ink-soft);
  }
  .contact-item { position: absolute; display: flex; align-items: center; gap: 9px; white-space: nowrap; }
  .contact-icon { width: 25px; height: 25px; display: block; }
  .contact-phone { left: 0; }
  .contact-fax { left: 150px; }
  .contact-email { left: 295px; }
  .contact-address { left: 455px; }
  .footer-band {
    position: absolute; left: 0; bottom: 0; width: 820px; height: 38px;
    background: linear-gradient(90deg, var(--blue-bright) 0%, var(--blue-mid) 55%, var(--blue-deep) 100%);
  }
  .footer-web {
    position: absolute; right: 46px; bottom: 11px;
    font-family: "Open Sans", sans-serif; font-weight: 700; font-size: 11px; color: #fff;
  }
</style>
</head>
<body>
  <main class="letterhead">
    <header>
      <div class="brand">
        <span class="brand-square"></span>
        <span class="brand-name">BRY7LEGAL</span>
      </div>
      <div class="principal">
        <div class="principal-name">ANSELMO R QUINTARA III</div>
        <div class="principal-title">ATTORNEY AT LAW</div>
      </div>
    </header>

    <section class="recipient">
      <div class="recipient-name">Name Surname</div>
      <div class="recipient-line">Attorney at Law</div>
      <div class="recipient-line">Address goes here. Street, City, Country</div>
      <div class="recipient-line">contact@yourmail.com</div>
      <div class="recipient-line">000-987-654-321</div>
    </section>
    <div class="letter-date">Date, 10 September, 2030</div>

    <section class="letter-body">
      <p>Lorem ipsum dolor sit amet, consectetur adipisicing elit, sed do eiusmod tempor incididunt ut labore et dolore magna aliqua. Ut enim ad minim veniam, quis nostrud exercitation ullamco laboris nisi ut aliquip ex ea commodo consequat. Duis aute irure dolor in reprehenderit in voluptate velit esse cillum dolore eu fugiat nulla pariatur. Excepteur sint occaecat cupidatat non proident, sunt in culpa qui officia deserunt mollit anim id est laborum. Sed ut perspiciatis unde omnis iste natus error sit voluptatem accusantium doloremque laudantium, totam rem aperiam, eaque ipsa quae ab illo inventore veritatis et quasi architecto beatae vitae dicta sunt explicabo. Nemo enim ipsam voluptatem quia voluptas sit aspernatur aut odit aut fugit, sed quia consequuntur magni dolores eos qui ratione voluptatem sequi nesciunt. Neque porro voluptatem sequi nesciunt. Nemo enim ipsam voluptatem quia voluptas.</p>
      <p>Lorem ipsum dolor sit amet, consectetur adipisicing elit, sed do eiusmod tempor incididunt ut labore et dolore magna aliqua. Ut enim ad minim veniam, quis nostrud exercitation ullamco laboris nisi ut aliquip ex ea commodo consequat. Duis aute irure dolor in reprehenderit in voluptate velit esse cillum dolore eu fugiat nulla pariatur. Excepteur sint occaecat cupidatat non proident, sunt in culpa qui officia deserunt mollit anim id est laborum. Sed ut perspiciatis unde omnis iste natus error sit voluptatem accusantium doloremque laudantium, totam rem aperiam, eaque ipsa quae ab illo inventore veritatis et quasi architecto beatae vitae dicta sunt explicabo. Nemo enim ipsam voluptatem quia voluptas sit aspernatur aut odit aut.</p>
      <p>Lorem ipsum dolor sit amet, consectetur adipisicing elit, sed do eiusmod tempor incididunt ut labore et dolore magna aliqua. Ut enim ad minim veniam, quis nostrud exercitation ullamco laboris nisi ut aliquip ex ea commodo consequat. .</p>
    </section>

    <div class="signature" role="img" aria-label="Handwritten signature of the sender"></div>

    <footer>
      <div class="contact-bar">
        <div class="contact-item contact-phone">
          <svg class="contact-icon" viewBox="0 0 25 25" aria-hidden="true"><rect width="25" height="25" fill="#1a8fd6"/><path d="M6 10c0-2 3-3 6.5-3S19 8 19 10v1h-3v-1.5h-7V11H6z M8 12h9l1 6H7z" fill="#fff"/><circle cx="12.5" cy="15" r="1.6" fill="#1a8fd6"/></svg>
          <span>877-482-6017</span>
        </div>
        <div class="contact-item contact-fax">
          <svg class="contact-icon" viewBox="0 0 25 25" aria-hidden="true"><rect width="25" height="25" fill="#1a8fd6"/><rect x="8.5" y="5.5" width="8" height="5" fill="#fff"/><rect x="6" y="10" width="13" height="7" rx="1" fill="#fff"/><rect x="8.5" y="15" width="8" height="5" fill="#fff" stroke="#1a8fd6" stroke-width="1"/></svg>
          <span>469-738-1452</span>
        </div>
        <div class="contact-item contact-email">
          <svg class="contact-icon" viewBox="0 0 25 25" aria-hidden="true"><rect width="25" height="25" fill="#1a8fd6"/><rect x="6" y="8" width="13" height="9" fill="none" stroke="#fff" stroke-width="1.2"/><path d="M6 8l6.5 5L19 8M6 17l5-4.5M19 17l-5-4.5" fill="none" stroke="#fff" stroke-width="1.2"/></svg>
          <span>bry@bry7legal.example</span>
        </div>
        <div class="contact-item contact-address">
          <svg class="contact-icon" viewBox="0 0 25 25" aria-hidden="true"><rect width="25" height="25" fill="#1a8fd6"/><path d="M12.5 5a5 5 0 0 1 5 5c0 4-5 10-5 10s-5-6-5-10a5 5 0 0 1 5-5z" fill="#fff"/><circle cx="12.5" cy="10" r="1.9" fill="#1a8fd6"/></svg>
          <span>2847 Larkspur Blvd, Ste 300, Dallas, TX 75204</span>
        </div>
      </div>

      <div class="footer-band"></div>
      <div class="footer-web">www.bry7legal.example</div>
    </footer>
  </main>
</body>
</html>
```